Naturopath Practitioner Card Design

I am a naturopath needing a design for a business card mainly to show that I am a naturopath and have some contact details to give to prospective clients. I am open minded about the design and what is on the second side of the card whether it just be some artwork or space for details, appointment times etc. Naturopathy is the practice of natural medicine that uses a holistic approach and incorporates herbal and nutritional medicine.

Industry/Entity Type

Business

Contact Information for Business Card

Tom Rudd NaturopathBHSc (Naturopathy) Member WHPG 0487 925 316 tom.rudd@mailexample.com www.tomruddnaturopathy.example.au

Requirements
Nice to have
• Would prefer some kind of original pattern/art work/logo rather than an image, not fussed if its very simple/basic
• I am open to any colour but think I would prefer a more earthy sandy clay etc type style than the greens that are commonly associated with naturopathy.
Should not have
• Don't really want to have generic stock images on it

```html
<!DOCTYPE html>
<html lang="en">
<head>
<meta charset="utf-8">
<title>Tom Rudd Naturopath – Business Card</title>
<link rel="stylesheet" href="https://fonts.googleapis.com/css2?family=Questrial&display=swap">
<style>
  :root {
    --bg: #dcdcdc;
    --card-light: #ececec;
    --clay: #5b441a;
    --clay-band: #6b5020;
    --gold: #d8b542;
    --gold-muted: #9c8430;
    --ink: #555555;
    --white: #ffffff;
  }
  * { margin: 0; padding: 0; box-sizing: border-box; }
  html, body {
    width: 1200px; height: 1021px; overflow: hidden;
    background: var(--bg);
    font-family: "Questrial", "Century Gothic", sans-serif;
  }
  .sheet {
    position: relative; width: 1200px; height: 1021px;
    display: flex; flex-direction: column; align-items: center;
    justify-content: center; gap: 60px;
  }
  .card {
    position: relative; width: 700px; height: 400px;
    box-shadow: 0 6px 18px rgba(0,0,0,.18);
    overflow: hidden;
  }
  /* Front */
  .card-front { background: var(--card-light); color: var(--ink); }
  .brand-mark {
    position: absolute; top: 52px; left: 0; right: 0;
    display: flex; align-items: center; justify-content: center; gap: 12px;
    color: var(--gold-muted); font-size: 22px;
  }
  .brand-dot { width: 16px; height: 16px; border-radius: 50%; background: var(--gold-muted); }
  .front-name {
    position: absolute; top: 108px; left: 0; right: 0; text-align: center;
    font-size: 38px; color: var(--ink); letter-spacing: .5px;
  }
  .front-credential {
    position: absolute; top: 162px; left: 0; right: 0; text-align: center;
    font-size: 15px; color: var(--gold-muted);
  }
  .contact-band {
    position: absolute; top: 222px; left: 0; right: 0; height: 46px;
    background: var(--clay-band); color: var(--white);
    display: flex; align-items: center; justify-content: center; gap: 40px;
    font-size: 20px;
  }
  .contact-item { display: flex; align-items: center; gap: 10px; }
  .contact-item svg { width: 20px; height: 20px; fill: var(--white); }
  .front-address {
    position: absolute; top: 292px; left: 0; right: 0;
    display: flex; align-items: center; justify-content: center; gap: 10px;
    font-size: 18px; color: var(--ink);
  }
  .front-address svg { width: 14px; height: 20px; fill: var(--gold-muted); }
  /* Back */
  .card-back { background: var(--clay); color: var(--gold); text-align: center; }
  .back-mark {
    position: absolute; top: 80px; left: 0; right: 0;
    display: flex; justify-content: center;
  }
  .back-mark .brand-dot { width: 34px; height: 34px; background: var(--gold); }
  .back-name {
    position: absolute; top: 132px; left: 0; right: 0;
    font-size: 54px; letter-spacing: 1px;
  }
  .back-title {
    position: absolute; top: 200px; left: 0; right: 0;
    font-size: 18px; letter-spacing: 9px;
  }
  .back-domain {
    position: absolute; top: 232px; left: 0; right: 0;
    font-size: 18px; color: var(--gold);
  }
  .back-web {
    position: absolute; top: 312px; left: 0; right: 0;
    font-size: 22px; color: #eeeeee; letter-spacing: .5px;
  }
</style>
</head>
<body>
<main class="sheet">
  <section class="card card-front" aria-label="Card front">
    <div class="brand-mark"><span class="brand-dot"></span><span>Tom Rudd</span></div>
    <h1 class="front-name">Tom Rudd</h1>
    <p class="front-credential">BHSc (Naturopathy) Member WHPG</p>
    <div class="contact-band">
      <span class="contact-item">
        <svg viewBox="0 0 24 24" aria-hidden="true"><path d="M6.6 10.8a15.1 15.1 0 0 0 6.6 6.6l2.2-2.2a1 1 0 0 1 1-.25 11.4 11.4 0 0 0 3.6.57 1 1 0 0 1 1 1V20a1 1 0 0 1-1 1A17 17 0 0 1 3 4a1 1 0 0 1 1-1h3.5a1 1 0 0 1 1 1c0 1.25.2 2.45.57 3.57a1 1 0 0 1-.25 1z"/></svg>
        0487 925 316
      </span>
      <span class="contact-item">
        <svg viewBox="0 0 24 24" aria-hidden="true"><path d="M2 5h20v14H2z M3.5 6.5 12 13l8.5-6.5" fill="none" stroke="#fff" stroke-width="2"/></svg>
        tom.rudd@mailexample.com
      </span>
    </div>
    <p class="front-address">
      <svg viewBox="0 0 14 20" aria-hidden="true"><path d="M7 0a7 7 0 0 0-7 7c0 5 7 13 7 13s7-8 7-13a7 7 0 0 0-7-7zm0 9.5A2.5 2.5 0 1 1 7 4.5a2.5 2.5 0 0 1 0 5z"/></svg>
      00, St. Name, City, State-0000
    </p>
  </section>

  <section class="card card-back" aria-label="Card back">
    <div class="back-mark"><span class="brand-dot"></span></div>
    <h2 class="back-name">Tom Rudd</h2>
    <p class="back-title">Naturopath</p>
    <p class="back-domain">tomruddnaturopathy.example.au</p>
    <p class="back-web">www.tomruddnaturopathy.example.au</p>
  </section>
</main>
</body>
</html>
```